Small Engine Post Card

We need a Small engine repair card design similar to our diesel Repair postcard (Sample TORLISK Diesel Card attached). The phone number will remain the same - there will be no website on this card address will be 3847 Bellvane Kellsboro, Texas 77418
Updates

Content for card If you have a small gas or diesel engine, call us, we service them all.• Lawn and Garden Tractors• Mowers• Chainsaws• Leaf Blowers• Water Pumps• Generators• Trimmers• Chipper/Shredders• Golf Carts• Air Compressors• Roto-Tillers• Snow Blowers• Zero-Turns• Go Carts• Pressure washers• Seasonal Services• Chain/blade Sharpening• Non-Highway Tire Repair281-650-25701522 Armada Houston, Texas77091 Added Friday, May 5, 2017

Target Market(s)

Lawn Care Providers

Font styles to use
Serif

Colors

Designer to choose colors to be used in the design.

Requirements
Must have
• Logos and Photos added
• • Lawn and Garden Tractors
• • Mowers
• • Chainsaws
• • Leaf Blowers
• • Water Pumps
• • Generators
• • Trimmers
• • Chipper/Shreaders
• • Golf Carts
• • Air Compressors
• • Roto-Tillers
• • Snow Blowers
• • Zero-Turns
• • Go Carts
• • Pressure washers
• • Seasonal Services
• • Chain/blade Sharpening
• • Non-Highway Tire Repair
• 281-473-9186
• 3847 Bellvane
• Houston, Texas
• 77091
Nice to have
• I have attached a photo with the manufacturer's logos - they will need to be added to the card front and back at the top and bottom - you can select one or two of the repair photo's as the main photo

```html
<!DOCTYPE html>
<html lang="en">
<head>
<meta charset="utf-8">
<title>TORLISK Diesel – Small Engine Postcard</title>
<link rel="stylesheet" href="https://fonts.googleapis.com/css2?family=Oswald:wght@400;500&family=Roboto+Condensed:wght@700&family=Open+Sans:wght@700&display=swap">
<style>
:root{
  --board:#5b5d5c;
  --panel-dark:#2c2c2e;
  --panel-mid:#3d3d40;
  --red:#c4161c;
  --red-deep:#8e0e12;
  --white:#ffffff;
  --silver:#d9d9d9;
  --photo-a:#3a3f45;
  --photo-b:#8b8f93;
}
*{margin:0;padding:0;box-sizing:border-box}
html,body{width:875px;height:1200px;overflow:hidden;background:var(--board)}
.board{position:relative;width:875px;height:1200px}
.card{position:absolute;width:614px;height:410px;overflow:hidden;background:var(--panel-dark)}
.card--front{left:109px;top:90px}
.card--back{left:164px;top:693px}
.photo{position:absolute;top:0;height:410px;width:380px}
.card--front .photo{left:0;background:linear-gradient(135deg,var(--photo-a),#6d7177 55%,var(--photo-b))}
.card--back .photo{right:0;background:linear-gradient(225deg,#6e6a66,#a59d96 45%,#4a4644)}
.shapes{position:absolute;left:0;top:0}
.brand-strip{position:absolute;background:var(--white);display:flex;align-items:center;justify-content:space-around;padding:0 6px;
  font-family:"Roboto Condensed",sans-serif;font-weight:700;font-size:7px;letter-spacing:.2px;text-transform:uppercase}
.brand-strip--top{top:0;height:21px}
.brand-strip--bottom{bottom:0;height:21px}
.card--front .brand-strip--top{left:165px;right:0}
.card--front .brand-strip--bottom{left:352px;right:0}
.card--back .brand-strip--top{left:0;width:460px}
.card--back .brand-strip--bottom{left:0;width:262px}
.brand{color:#222}
.brand--red{color:var(--red)}
.brand--gold{color:#c9a227}
.brand--blue{color:#1f4ea1}
.brand--green{color:#3c8a3a}
.services{position:absolute;top:42px;display:grid;grid-template-columns:132px 132px;
  font-family:"Roboto Condensed",sans-serif;font-weight:700;font-size:8.6px;color:var(--white);text-transform:uppercase;line-height:13.1px}
.services ul{list-style:none}
.services li{position:relative;padding-left:9px;white-space:nowrap}
.services li::before{content:"";position:absolute;left:0;top:4px;width:5px;height:5px;border-radius:50%;background:var(--red)}
.card--front .services{left:328px}
.card--back .services{left:31px}
.contact{position:absolute;top:170px;height:70px;text-align:center;color:var(--white)}
.card--front .contact{left:336px;width:278px}
.card--back .contact{left:0;width:292px}
.phone{font-family:"Open Sans",sans-serif;font-weight:700;font-size:28px;line-height:34px;margin-top:11px;display:flex;align-items:center;justify-content:center;gap:5px}
.phone svg{width:24px;height:24px}
.address{font-family:"Roboto Condensed",sans-serif;font-weight:700;font-size:13.5px;line-height:18px;text-transform:uppercase;white-space:nowrap}
.cards-note{position:absolute;top:254px;font-family:"Roboto Condensed",sans-serif;font-weight:700;font-size:10px;color:var(--white);text-align:center}
.card--front .cards-note{left:352px;width:240px}
.card--back .cards-note{left:0;width:270px}
.wordmark{position:absolute;top:288px;text-align:center;font-family:"Oswald",sans-serif;font-weight:500;color:var(--white)}
.card--front .wordmark{left:356px;width:240px}
.card--back .wordmark{left:24px;width:240px}
.wordmark__name{font-size:36px;line-height:40px;letter-spacing:3px;display:block}
.wordmark__sub{font-size:15px;line-height:18px;letter-spacing:4px;display:block}
.pitch{position:absolute;top:262px;font-family:"Oswald",sans-serif;font-weight:400;color:var(--white);text-transform:uppercase;text-shadow:0 1px 3px rgba(0,0,0,.5)}
.card--front .pitch{left:14px;text-align:left}
.card--back .pitch{right:15px;text-align:right}
.pitch__lead{font-size:37px;line-height:44px;font-weight:500}
.pitch__body{font-size:23px;line-height:26.5px}
</style>
</head>
<body>
<main class="board">

  <section class="card card--front">
    <div class="photo" role="img" aria-label="Photo of a technician servicing a small engine air filter in a workshop"></div>
    <svg class="shapes" width="614" height="410" viewBox="0 0 614 410" aria-hidden="true">
      <defs>
        <linearGradient id="panelFront" x1="0" y1="0" x2="0" y2="1"><stop offset="0" stop-color="#3d3d40"/><stop offset="1" stop-color="#262628"/></linearGradient>
        <linearGradient id="bandFront" x1="0" y1="0" x2="1" y2="0"><stop offset="0" stop-color="#8e0e12"/><stop offset=".5" stop-color="#c4161c"/><stop offset="1" stop-color="#a51217"/></linearGradient>
        <clipPath id="panelClipFront"><path d="M150,0 L614,0 L614,410 L352,410 C330,260 270,110 150,0 Z"/></clipPath>
      </defs>
      <path d="M150,0 L614,0 L614,410 L352,410 C330,260 270,110 150,0 Z" fill="url(#panelFront)"/>
      <rect x="250" y="170" width="364" height="70" fill="url(#bandFront)" clip-path="url(#panelClipFront)"/>
      <path d="M60,0 C200,90 300,230 324,410" fill="none" stroke="#d9d9d9" stroke-width="4"/>
      <path d="M92,0 C240,100 320,240 336,410 L352,410 C330,260 270,110 150,0 Z" fill="#c4161c"/>
    </svg>
    <div class="brand-strip brand-strip--top">
      <span class="brand">Ekhorn</span><span class="brand brand--gold">Cubbard</span><span class="brand brand--blue">Kestrel</span><span class="brand">Bramwell</span><span class="brand brand--red">Redlow</span><span class="brand">Marlow</span><span class="brand brand--green">Tandem</span><span class="brand brand--gold">Halvane</span><span class="brand brand--green">Bolder</span><span class="brand brand--red">Bexa</span>
    </div>
    <div class="services">
      <ul><li>Lawn and Garden Tractors</li><li>Mowers</li><li>Chainsaws</li><li>Leaf Blowers</li><li>Water Pumps</li><li>Generators</li><li>Trimmers</li><li>Chipper/Shredders</li><li>Golf Carts</li></ul>
      <ul><li>Air Compressors</li><li>Roto-Tillers</li><li>Snow Blowers</li><li>Zero-Turns</li><li>Go Carts</li><li>Pressure Washers</li><li>Seasonal Services</li><li>Chain/Blade Sharpening</li><li>Non-Highway Tire Repair</li></ul>
    </div>
    <div class="contact">
      <p class="phone"><svg viewBox="0 0 24 24" aria-hidden="true"><circle cx="12" cy="12" r="10.5" fill="none" stroke="#fff" stroke-width="2"/><path d="M8.5 6.5c.6-.4 1.3-.2 1.6.4l.9 1.8c.2.5.1 1-.3 1.4l-.7.6c.6 1.3 1.6 2.4 2.9 3l.6-.7c.4-.4.9-.5 1.4-.3l1.8.9c.6.3.8 1 .4 1.6-.8 1.3-2.3 1.8-3.7 1.2-2.7-1.1-4.8-3.2-5.9-5.9-.5-1.4 0-2.9 1-3.7z" fill="#fff"/></svg>281-473-9186</p>
      <p class="address">3847 Bellvane, Kellsboro, Texas 77418</p>
    </div>
    <p class="cards-note">We accept all major credit cards</p>
    <div class="wordmark"><span class="wordmark__name">TORLISK</span><span class="wordmark__sub">DIESEL</span></div>
    <div class="pitch">
      <p class="pitch__lead">Call us</p>
      <p class="pitch__body">If you have a small<br>gas or diesel engine,<br>we service them all.</p>
    </div>
    <div class="brand-strip brand-strip--bottom">
      <span class="brand">Ferrow</span><span class="brand brand--red">Ostend</span><span class="brand brand--red">Lyndor</span><span class="brand">Quarry</span><span class="brand brand--gold">Tavik</span><span class="brand brand--blue">Brisk</span><span class="brand brand--red">Ryland</span>
    </div>
  </section>

  <section class="card card--back">
    <div class="photo" role="img" aria-label="Close-up photo of a feeler gauge adjusting small engine valves"></div>
    <svg class="shapes" width="614" height="410" viewBox="0 0 614 410" aria-hidden="true">
      <defs>
        <linearGradient id="panelBack" x1="0" y1="0" x2="0" y2="1"><stop offset="0" stop-color="#3d3d40"/><stop offset="1" stop-color="#262628"/></linearGradient>
        <linearGradient id="bandBack" x1="0" y1="0" x2="1" y2="0"><stop offset="0" stop-color="#a51217"/><stop offset=".5" stop-color="#c4161c"/><stop offset="1" stop-color="#8e0e12"/></linearGradient>
        <clipPath id="panelClipBack"><path d="M150,0 L614,0 L614,410 L352,410 C330,260 270,110 150,0 Z"/></clipPath>
      </defs>
      <g transform="translate(614,0) scale(-1,1)">
        <path d="M150,0 L614,0 L614,410 L352,410 C330,260 270,110 150,0 Z" fill="url(#panelBack)"/>
        <rect x="250" y="170" width="364" height="70" fill="url(#bandBack)" clip-path="url(#panelClipBack)"/>
        <path d="M60,0 C200,90 300,230 324,410" fill="none" stroke="#d9d9d9" stroke-width="4"/>
        <path d="M92,0 C240,100 320,240 336,410 L352,410 C330,260 270,110 150,0 Z" fill="#c4161c"/>
      </g>
    </svg>
    <div class="brand-strip brand-strip--top">
      <span class="brand">Ekhorn</span><span class="brand brand--gold">Cubbard</span><span class="brand brand--blue">Kestrel</span><span class="brand">Bramwell</span><span class="brand brand--red">Redlow</span><span class="brand">Marlow</span><span class="brand brand--green">Tandem</span><span class="brand brand--gold">Halvane</span><span class="brand brand--green">Bolder</span><span class="brand brand--red">Bexa</span>
    </div>
    <div class="services">
      <ul><li>Lawn and Garden Tractors</li><li>Mowers</li><li>Chainsaws</li><li>Leaf Blowers</li><li>Water Pumps</li><li>Generators</li><li>Trimmers</li><li>Chipper/Shredders</li><li>Golf Carts</li></ul>
      <ul><li>Air Compressors</li><li>Roto-Tillers</li><li>Snow Blowers</li><li>Zero-Turns</li><li>Go Carts</li><li>Pressure Washers</li><li>Seasonal Services</li><li>Chain/Blade Sharpening</li><li>Non-Highway Tire Repair</li></ul>
    </div>
    <div class="contact">
      <p class="phone"><svg viewBox="0 0 24 24" aria-hidden="true"><circle cx="12" cy="12" r="10.5" fill="none" stroke="#fff" stroke-width="2"/><path d="M8.5 6.5c.6-.4 1.3-.2 1.6.4l.9 1.8c.2.5.1 1-.3 1.4l-.7.6c.6 1.3 1.6 2.4 2.9 3l.6-.7c.4-.4.9-.5 1.4-.3l1.8.9c.6.3.8 1 .4 1.6-.8 1.3-2.3 1.8-3.7 1.2-2.7-1.1-4.8-3.2-5.9-5.9-.5-1.4 0-2.9 1-3.7z" fill="#fff"/></svg>281-473-9186</p>
      <p class="address">3847 Bellvane, Kellsboro, Texas 77418</p>
    </div>
    <p class="cards-note">We accept all major credit cards</p>
    <div class="wordmark"><span class="wordmark__name">TORLISK</span><span class="wordmark__sub">DIESEL</span></div>
    <div class="pitch">
      <p class="pitch__lead">Call us</p>
      <p class="pitch__body">If you have a small<br>gas or diesel engine,<br>we service them all.</p>
    </div>
    <div class="brand-strip brand-strip--bottom">
      <span class="brand">Ferrow</span><span class="brand brand--red">Ostend</span><span class="brand brand--red">Lyndor</span><span class="brand">Quarry</span><span class="brand brand--gold">Tavik</span><span class="brand brand--blue">Brisk</span><span class="brand brand--red">Ryland</span>
    </div>
  </section>

</main>
</body>
</html>
```